Tender / Request for Quotation response template

KELVARA42 is a small consulting company that works in management consulting with a particular emphasis on tourism, sport, major events and general commercial. our clients range from government , councils, private businesses and industry associations.

we are regularly asked to submit detailed quotes or tender responses and we use our own PowerPoint template to do so as we find it its generally easier to work with.

our website provides more detail : www.kelvara42.com.au the colour of the blue in logo is #000033

our submissions range from 30 pages to 100 pages depending on the size and scale of the project - so we need flexibility with the templates.

Our submissions generally include cover page and table of contents and then
1. Project overview
2. About KELVARA42
3. The project team including bios
4. Initial Insights
5. importance of sustainability
6. Project methodology - example being
6.1 situation analysis
- research
- consultation and engagement
- relevant audits
- relevant economic analysis including graphs
- gap analysis
- SWOT
6.2 Issues and opportunities
6.3 draft report
6.4 final report
7. Case studies and previous relevant work
8. Project timeline
9. Project budget
10. Insurance and referees

we use many graphs and tables from excel and images generally sourced from the web. we also use icons as appropriate so we need graph templates - column, bar / pie etc and table templates.

the feel is on the formal corporate side given the size and scale of projects and clients but with bright and clear graphics and photos.

i have attached 2 copies of confidential submissions that we have made in recent weeks. one long form and one short form to give you an idea of the flexibility we need in the submission process.

if we are happy with the proposed PowerPoint tender submission template we would then look to have a similar one created to use in the development of the actual reports themselves .

hopefully this provides enough information but if not please reach out for more information

our logo and general format are in the attached examples

Target Market(s)

government, council, corporates and private businesses

Industry/Entity Type

management consulting with emphasis on tourism sport major events nd general commerical

Other font styles liked:
• we usually use calbiri but open to other standard microsoft off the shelf fonts

Colors
0054AA
0677BA
7BADD7
CADEEF
E8F1F8
0094D4
00A9DD
6FCCEA
C7EBF8
E9F6FB

Requirements
Must have
• page for each of the sections detailed in the project brief. image placement - small and large, table and graph formats,

```html
<!DOCTYPE html>
<html lang="en">
<head>
<meta charset="utf-8">
<title>KELVARA42 Tender Response Template</title>
<link href="https://fonts.googleapis.com/css2?family=Roboto:wght@400;500;700&display=swap" rel="stylesheet">
<style>
:root{
  --page:#d6d6d6;
  --slide:#ffffff;
  --blue:#12a4dc;
  --blue-deep:#0677ba;
  --blue-pale:#c7ebf8;
  --ring:#6fccea;
  --ink:#2b2b2b;
  --muted:#555;
  --card:#eeeeee;
}
*{box-sizing:border-box;margin:0;padding:0}
html,body{width:1200px;height:3968px;overflow:hidden}
body{background:var(--page);font-family:'Roboto',Arial,sans-serif;color:var(--ink);position:relative}
.slide{position:absolute;left:63px;width:1074px;height:604px;background:var(--slide);overflow:hidden;box-shadow:0 1px 3px rgba(0,0,0,.15)}
.header{position:absolute;top:0;right:0;height:80px;background:var(--blue);display:flex;align-items:center}
.header.slant{clip-path:polygon(0 0,100% 0,100% 100%,60px 100%)}
.header h2{color:#fff;font-weight:700;font-size:31px;letter-spacing:.3px}
.brand{position:absolute;right:38px;top:12px;display:flex;flex-direction:column;align-items:center;color:#fff}
.brand .mark{width:34px;height:34px;border:2px solid #fff;border-radius:50%}
.brand span{font-size:13px;font-weight:500;margin-top:4px;letter-spacing:.5px}
.bullets{list-style:none;position:absolute}
.bullets li{position:relative;padding-left:22px;font-size:10.5px;line-height:1.75;color:var(--muted);margin-bottom:15px}
.bullets li::before{content:"";position:absolute;left:0;top:3px;width:11px;height:11px;border-radius:50%;background:var(--blue)}
.bullets li::after{content:"";position:absolute;left:3px;top:6.5px;width:4px;height:4px;border-top:1.5px solid #fff;border-right:1.5px solid #fff;transform:rotate(45deg)}
.bullets.tight li{margin-bottom:8px}
.footer{position:absolute;bottom:10px;height:49px;background:var(--blue);display:flex;align-items:center;color:#fff;font-size:7.5px;font-weight:700}
.footer.left{left:0;width:605px;border-radius:0 25px 25px 0;padding-left:34px}
.footer.right{right:0;width:604px;border-radius:25px 0 0 25px;padding-left:14px}
.f-item{display:flex;align-items:center;gap:8px}
.f-item svg{flex:none}
.f-num{width:33px;height:33px;border-radius:50%;background:#fff;color:var(--blue);font-size:15px;font-weight:700;display:flex;align-items:center;justify-content:center}
.lead{position:absolute;font-size:12px;line-height:1.85;text-align:center}
.photo{position:absolute}
/* team */
.member{position:absolute;top:222px;width:186px;height:208px;border-radius:50%;background:var(--card);box-shadow:0 3px 6px rgba(0,0,0,.12);text-align:center;padding-top:30px}
.member .pic{width:64px;height:64px;margin:0 auto 10px;border:3px solid var(--ring);background:linear-gradient(#8aa0b6,#5f6f80)}
.member b{display:block;font-size:9.5px;margin-bottom:4px}
.member p{font-size:9.5px;line-height:1.8;color:var(--muted)}
/* methodology */
.step{position:absolute;top:220px;width:150px;height:150px;margin-left:-75px}
.step-label{position:absolute;width:170px;margin-left:-85px;text-align:center;font-size:12px;font-weight:700;line-height:1.3}
.arrow{position:absolute;top:287px;width:34px;margin-left:-17px}
/* timeline */
.tl-date{position:absolute;top:184px;width:140px;margin-left:-70px;text-align:center;font-size:11px}
.tl-node{position:absolute;width:100px;height:100px;margin-left:-50px;top:332px;border-radius:50%;border:3px solid var(--blue);display:flex;align-items:center;justify-content:center}
.tl-node i{width:84px;height:84px;border-radius:50%;background:var(--blue);display:flex;align-items:center;justify-content:center}
.tl-label{position:absolute;top:455px;width:170px;margin-left:-85px;text-align:center;font-size:11.5px;font-weight:700;line-height:1.45}
.tl-tag{position:absolute;left:50px;font-size:12px;font-weight:700}
</style>
</head>
<body>

<!-- 1 Project overview -->
<section class="slide" style="top:42px">
  <svg class="photo" width="440" height="450" viewBox="0 0 440 450" role="img" aria-label="Photo of cyclists riding a coastal road">
    <defs>
      <clipPath id="c1"><circle cx="180" cy="170" r="245"/></clipPath>
      <linearGradient id="g1" x1="0" y1="0" x2="0" y2="1"><stop offset="0" stop-color="#a9c8dc"/><stop offset=".4" stop-color="#8a9a78"/><stop offset="1" stop-color="#9b8a62"/></linearGradient>
    </defs>
    <rect width="440" height="450" fill="url(#g1)" clip-path="url(#c1)"/>
    <circle cx="180" cy="170" r="251" fill="none" stroke="#fff" stroke-width="8"/>
    <circle cx="180" cy="170" r="258" fill="none" stroke="var(--blue)" stroke-width="7"/>
  </svg>
  <div class="header" style="left:405px;padding-left:40px"><h2>1. PROJECT OVERVIEW</h2></div>
  <div class="brand"><div class="mark"></div><span>KELVARA42</span></div>
  <ul class="bullets" style="left:465px;top:128px;width:570px">
    <li>KELVARA42 has been requested to provide a quotation and submission to assist Heritage Trust Southland (HTS) in undertaking a feasibility assessment of the development of a Fashion and Dress Resource centre.</li>
    <li>HTS has a significant Costume Collection and is looking at how best to realise this asset for HTS and the wider community. The Costume Collection is a nationally significant collection of fashion and dress and has been collecting items since 1961.</li>
    <li>The collection now includes over 7,000 items. The breadth of the collection is considerable. Its strength spans the gold-rush era through the land-boom of the 1880s. A growing and developing collecting area is mid-twentieth century costume to the present day.</li>
    <li>Public awareness of the collection is increasing and the outgoing loans to major public institutions such as the Southland State Gallery and Ridgefield Art Gallery bring further attention to the Trust's collection in the wider fashion research community.</li>
    <li>Currently the Costume Collection is housed in multiple unsatisfactory storage facilities and the future preservation of the collection is at risk if this continues.</li>
    <li>A different solution is required to ensure the preservation and presentation of the Costume Collection for the future. The proposed Fashion and Dress Resource centre is one suggested option. Better exploitation and preservation of the Collection resources is a key driver in the HTS new Strategic Plan.</li>
  </ul>
  <div class="footer left">
    <div class="f-item" style="width:205px"><svg width="14" height="11" viewBox="0 0 14 11"><rect x=".5" y=".5" width="13" height="10" rx="2" fill="#fff"/><path d="M2 2.5l5 4 5-4" stroke="var(--blue)" fill="none"/></svg>info@kelvara42.com.au</div>
    <div class="f-item" style="width:140px"><svg width="16" height="16" viewBox="0 0 16 16"><rect width="16" height="16" rx="3" fill="#fff"/><path d="M5 3l2 3-1 1c.7 1.4 1.6 2.3 3 3l1-1 3 2-1 2c-4 0-8-4-8-8z" fill="var(--blue)"/></svg>+61 400 000 123</div>
    <div class="f-item" style="width:180px"><svg width="18" height="18" viewBox="0 0 18 18"><rect width="18" height="18" rx="3" fill="#fff"/><path d="M9 3a4 4 0 0 1 4 4c0 3-4 8-4 8S5 10 5 7a4 4 0 0 1 4-4z" fill="var(--blue)"/><circle cx="9" cy="7" r="1.5" fill="#fff"/></svg><span>Melbourne, Sydney, Brisbane,<br>Perth, Gold Coast, Hobart</span></div>
    <div class="f-num">01</div>
  </div>
</section>

<!-- 2 About -->
<section class="slide" style="top:691px">
  <div class="header slant" style="left:448px;padding-left:95px"><h2>2.ABOUT KELVARA42</h2></div>
  <div class="brand"><div class="mark"></div><span>KELVARA42</span></div>
  <div style="position:absolute;left:40px;top:105px;font-size:15px;font-weight:700">WE BRING TO THIS EXTREMELY IMPORTANT PROJECT:</div>
  <ul class="bullets" style="left:38px;top:135px;width:572px">
    <li>The most experienced project team in Australia in nature based tourism, events and the visitor economy. We understand the challenges and opportunities presented by utilising Crown land.</li>
    <li>Each member of the project team and specialist team are experts in their field. They are not generalist consultants. All KELVARA42 project work will be undertaken by these experts and NOT delegated to an inexperienced junior consultant.</li>
    <li>The project team are all industry leaders of high standing that will bring insights and outcomes based on over 100 years of collective experience.</li>
    <li>Our team have all sat on both the client and consultant side. We know exactly what is required to deliver a successful outcome for the client. For that reason, we operate under a co-design model.</li>
    <li>We bring extensive local knowledge of the Coastal Ridge Road region, its visitor economy, its accommodation offerings and experience working with Aboriginal land custodians.</li>
    <li>We have a laser like focus on stakeholder &amp; community participation both through direct engagement and by survey. We understand and have great respect of the need for Social Licence and Sustainability of outcomes.</li>
    <li>We bring passion and energy to our projects. We love our industry and our jobs. We have fun ensuring the best outcomes for our clients.</li>
  </ul>
  <div class="photo" role="img" aria-label="Photo of a traveller in a sun hat overlooking a beach" style="left:640px;top:111px;width:395px;height:357px;background:linear-gradient(160deg,#7fb3d6 0%,#4f9fbf 40%,#d6c29a 70%,#8c7a66 100%)">
    <div style="position:absolute;left:22px;top:22px;right:16px;bottom:18px;border:3px solid #fff"></div>
  </div>
  <div class="footer right">
    <div class="f-num" style="margin-right:50px">02</div>
    <div class="f-item" style="width:195px"><svg width="18" height="18" viewBox="0 0 18 18"><rect width="18" height="18" rx="3" fill="#fff"/><path d="M9 3a4 4 0 0 1 4 4c0 3-4 8-4 8S5 10 5 7a4 4 0 0 1 4-4z" fill="var(--blue)"/><circle cx="9" cy="7" r="1.5" fill="#fff"/></svg><span>Melbourne, Sydney, Brisbane,<br>Perth, Gold Coast, Hobart</span></div>
    <div class="f-item" style="width:140px"><svg width="16" height="16" viewBox="0 0 16 16"><rect width="16" height="16" rx="3" fill="#fff"/><path d="M5 3l2 3-1 1c.7 1.4 1.6 2.3 3 3l1-1 3 2-1 2c-4 0-8-4-8-8z" fill="var(--blue)"/></svg>+61 400 000 123</div>
    <div class="f-item"><svg width="14" height="11" viewBox="0 0 14 11"><rect x=".5" y=".5" width="13" height="10" rx="2" fill="#fff"/><path d="M2 2.5l5 4 5-4" stroke="var(--blue)" fill="none"/></svg>info@kelvara42.com.au</div>
  </div>
</section>

<!-- 3 Team -->
<section class="slide" style="top:1341px">
  <div class="header slant" style="left:448px;padding-left:70px"><h2>3.THE PROJECT TEAM</h2></div>
  <div class="brand"><div class="mark"></div><span>KELVARA42</span></div>
  <p class="lead" style="left:150px;top:108px;width:780px;font-weight:700;font-size:11.5px">The project will be overseen by a team of four highly experienced tourism and event specialists, supported by a senior sustainable tourism statutory planner (if required)</p>
  <div class="member" style="left:26px"><div class="pic" role="img" aria-label="Portrait photo of team member"></div><b>Mark Delaney</b><p>Project Leader<br>Tourism &amp; Major Events<br>Specialist</p></div>
  <div class="member" style="left:226px"><div class="pic" role="img" aria-label="Portrait photo of team member"></div><b>Dr Helen Marsh</b><p>Sustainability &amp; Nature Based<br>Tourism Specialist</p></div>
  <div class="member" style="left:427px"><div class="pic" role="img" aria-label="Portrait photo of team member"></div><b>Tom Whitfield</b><p>Event Attraction<br>&amp; Consumer Research<br>Specialist</p></div>
  <div class="member" style="left:629px"><div class="pic" role="img" aria-label="Portrait photo of team member"></div><b>Graham Rowe AM</b><p>Event Planning &amp; Facilities<br>Management Specialist</p></div>
  <div class="member" style="left:836px"><div class="pic" role="img" aria-label="Portrait photo of team member"></div><b>Sophie Lennard</b><p>Strategic Planning &amp;<br>Sustainable Tourism Expert</p></div>
  <div class="footer left">
    <div class="f-item" style="width:205px"><svg width="14" height="11" viewBox="0 0 14 11"><rect x=".5" y=".5" width="13" height="10" rx="2" fill="#fff"/><path d="M2 2.5l5 4 5-4" stroke="var(--blue)" fill="none"/></svg>info@kelvara42.com.au</div>
    <div class="f-item" style="width:140px"><svg width="16" height="16" viewBox="0 0 16 16"><rect width="16" height="16" rx="3" fill="#fff"/><path d="M5 3l2 3-1 1c.7 1.4 1.6 2.3 3 3l1-1 3 2-1 2c-4 0-8-4-8-8z" fill="var(--blue)"/></svg>+61 400 000 123</div>
    <div class="f-item" style="width:180px"><svg width="18" height="18" viewBox="0 0 18 18"><rect width="18" height="18" rx="3" fill="#fff"/><path d="M9 3a4 4 0 0 1 4 4c0 3-4 8-4 8S5 10 5 7a4 4 0 0 1 4-4z" fill="var(--blue)"/><circle cx="9" cy="7" r="1.5" fill="#fff"/></svg><span>Melbourne, Sydney, Brisbane,<br>Perth, Gold Coast, Hobart</span></div>
    <div class="f-num">03</div>
  </div>
</section>

<!-- 4 Sustainability -->
<section class="slide" style="top:1990px">
  <div class="header slant" style="left:363px;padding-left:92px"><h2>4. SUSTAINABILITY</h2></div>
  <div class="brand"><div class="mark"></div><span>KELVARA42</span></div>
  <div style="position:absolute;left:35px;top:140px;width:400px;height:357px;border:5px solid var(--ring)">
    <div style="position:absolute;left:55px;top:40px;width:280px;height:90px;background:#eef3e6;border-radius:6px"></div>
    <div style="position:absolute;left:25px;top:185px;width:310px;height:125px;background:#eeeeee;border-radius:4px"></div>
  </div>
  <ul class="bullets tight" style="left:465px;top:128px;width:580px">
    <li>One of KELVARA42 core principles is that tourism and tourism products must be sustainable. Sustainability in that context means ensuring adherence to world's best practice in regenerative and sustainable tourism. We know that HTS also supports that philosophy.</li>
    <li>In our tourism feasibility work we align with the guidelines of the World Responsible Travel Council (WRTC) and Green Journeys Alliance who has adapted those WRTC guidelines into an Australian context .</li>
    <li>The role of WRTC is to enhance the creation of sustainable tourism destinations and products around the world. In particular, its aim is that:<br>Tourism fulfils its potential as a vehicle for social, cultural, and economic good while removing and avoiding any negative impacts from its activities in terms of environmental and social impacts.</li>
    <li style="margin-bottom:3px">To do this it has created a four pillar model that includes:</li>
    <li style="margin-bottom:3px">Demonstration of effective sustainable management.</li>
    <li style="margin-bottom:3px">Maximizing social and economic benefits to the local community and minimize negative impacts.</li>
    <li style="margin-bottom:3px">Maximize benefits to cultural heritage and minimize negative impacts.</li>
    <li style="margin-bottom:3px">Maximize benefits to the environment and minimize negative impacts.</li>
    <li style="margin-bottom:3px">This WRTC framework has become the leading framework for sustainable tourism around the world, with local nuances adopted by regional ecotourism bodies such as Green Journeys Alliance.</li>
    <li>We will apply this model throughout this project.</li>
  </ul>
  <div class="footer right">
    <div class="f-num" style="margin-right:50px">04</div>
    <div class="f-item" style="width:195px"><svg width="18" height="18" viewBox="0 0 18 18"><rect width="18" height="18" rx="3" fill="#fff"/><path d="M9 3a4 4 0 0 1 4 4c0 3-4 8-4 8S5 10 5 7a4 4 0 0 1 4-4z" fill="var(--blue)"/><circle cx="9" cy="7" r="1.5" fill="#fff"/></svg><span>Melbourne, Sydney, Brisbane,<br>Perth, Gold Coast, Hobart</span></div>
    <div class="f-item" style="width:140px"><svg width="16" height="16" viewBox="0 0 16 16"><rect width="16" height="16" rx="3" fill="#fff"/><path d="M5 3l2 3-1 1c.7 1.4 1.6 2.3 3 3l1-1 3 2-1 2c-4 0-8-4-8-8z" fill="var(--blue)"/></svg>+61 400 000 123</div>
    <div class="f-item"><svg width="14" height="11" viewBox="0 0 14 11"><rect x=".5" y=".5" width="13" height="10" rx="2" fill="#fff"/><path d="M2 2.5l5 4 5-4" stroke="var(--blue)" fill="none"/></svg>info@kelvara42.com.au</div>
  </div>
</section>

<!-- 5 Methodology -->
<section class="slide" style="top:2640px">
  <div class="header slant" style="left:363px;padding-left:64px"><h2>5. METHODOLOGY – FINAL REPORT</h2></div>
  <div class="brand"><div class="mark"></div><span>KELVARA42</span></div>
  <p class="lead" style="left:440px;top:105px;width:600px;font-size:12px">Once each of the above stages has been completed, we will prepare a final report that encompasses the details and insights from the project with key recommendations on the overall feasibility of the project.</p>

  <svg style="position:absolute;left:0;top:0" width="1074" height="604" viewBox="0 0 1074 604" aria-hidden="true">
    <defs>
      <g id="ring">
        <circle r="74" fill="none" stroke="var(--ring)" stroke-width="2"/>
        <circle r="62" fill="#fff" stroke="#e3e3e3" stroke-width="5"/>
      </g>
    </defs>
    <g transform="translate(169,297)"><use href="#ring"/><path d="M-52,-50 A74 74 0 0 1 52,-50" fill="none" stroke="var(--blue)" stroke-width="8"/>
      <rect x="-17" y="-22" width="28" height="36" rx="2" fill="none" stroke="#222" stroke-width="3"/><path d="M-11-12h16M-11-4h16M-11 4h10" stroke="#222" stroke-width="2.5"/><circle cx="12" cy="12" r="8" fill="#fff" stroke="#222" stroke-width="3"/><path d="M18 18l7 7" stroke="#222" stroke-width="3"/></g>
    <g transform="translate(362,297)"><use href="#ring"/><path d="M-52,50 A74 74 0 0 0 52,50" fill="none" stroke="var(--blue)" stroke-width="8"/>
      <rect x="-22" y="2" width="6" height="18" fill="#222"/><rect x="-13" y="-6" width="6" height="26" fill="#222"/><rect x="-4" y="6" width="6" height="14" fill="#222"/><path d="M8-18h16M8-10h16M8-2h16" stroke="#222" stroke-width="3"/><circle cx="-12" cy="-16" r="7" fill="#222"/></g>
    <g transform="translate(554,297)"><use href="#ring"/><path d="M-52,-50 A74 74 0 0 1 52,-50" fill="none" stroke="var(--blue)" stroke-width="8"/>
      <rect x="-16" y="-24" width="30" height="40" rx="2" fill="none" stroke="#222" stroke-width="3"/><path d="M-10-14h18M-10-6h18M-10 2h12" stroke="#222" stroke-width="2.5"/><circle cx="-10" cy="14" r="9" fill="#222"/></g>
    <g transform="translate(744,297)"><use href="#ring"/><path d="M-52,50 A74 74 0 0 0 52,50" fill="none" stroke="var(--blue)" stroke-width="8"/>
      <path d="M-16-24h22l10 10v38h-32z" fill="#222"/><path d="M-10 16v-8M-4 16v-14M2 16v-10M8 16v-18" stroke="#fff" stroke-width="3"/></g>
    <g transform="translate(933,297)"><use href="#ring"/><path d="M-52,-50 A74 74 0 0 1 52,-50" fill="none" stroke="var(--blue)" stroke-width="8"/>
      <circle cy="-8" r="14" fill="none" stroke="#222" stroke-width="3"/><path d="M-6-8l4 4 8-8" stroke="#222" stroke-width="3" fill="none"/><path d="M-26 14q26 16 52 0" stroke="#222" stroke-width="4" fill="none"/></g>
    <g stroke="#222" stroke-width="3" fill="none">
      <path d="M248 297h28M268 290l8 7-8 7"/><path d="M441 297h28M461 290l8 7-8 7"/><path d="M632 297h28M652 290l8 7-8 7"/><path d="M822 297h28M842 290l8 7-8 7"/>
    </g>
  </svg>
  <div class="step-label" style="left:159px;top:393px">SITUATION<br>ANALYSIS</div>
  <div class="step-label" style="left:350px;top:387px">MARKET RESEARCH</div>
  <div class="step-label" style="left:563px;top:384px">ISSUES &amp;<br>&amp;OPPORTUNITIES</div>
  <div class="step-label" style="left:739px;top:391px">FINANCIAL ANALYSIS</div>
  <div class="step-label" style="left:940px;top:395px">RECOMMENDATIONS</div>

  <div class="footer left">
    <div class="f-item" style="width:205px"><svg width="14" height="11" viewBox="0 0 14 11"><rect x=".5" y=".5" width="13" height="10" rx="2" fill="#fff"/><path d="M2 2.5l5 4 5-4" stroke="var(--blue)" fill="none"/></svg>info@kelvara42.com.au</div>
    <div class="f-item" style="width:140px"><svg width="16" height="16" viewBox="0 0 16 16"><rect width="16" height="16" rx="3" fill="#fff"/><path d="M5 3l2 3-1 1c.7 1.4 1.6 2.3 3 3l1-1 3 2-1 2c-4 0-8-4-8-8z" fill="var(--blue)"/></svg>+61 400 000 123</div>
    <div class="f-item" style="width:180px"><svg width="18" height="18" viewBox="0 0 18 18"><rect width="18" height="18" rx="3" fill="#fff"/><path d="M9 3a4 4 0 0 1 4 4c0 3-4 8-4 8S5 10 5 7a4 4 0 0 1 4-4z" fill="var(--blue)"/><circle cx="9" cy="7" r="1.5" fill="#fff"/></svg><span>Melbourne, Sydney, Brisbane,<br>Perth, Gold Coast, Hobart</span></div>
    <div class="f-num">05</div>
  </div>
</section>

<!-- 6 Timeline -->
<section class="slide" style="top:3290px">
  <div class="header slant" style="left:448px;padding-left:95px"><h2>6. PROJECT TIMELINE</h2></div>
  <div class="brand"><div class="mark"></div><span>KELVARA42</span></div>

  <div class="tl-date" style="left:194px">10 September 2023</div>
  <div class="tl-date" style="left:350px">27 October 2023*</div>
  <div class="tl-date" style="left:491px">27 October 2023</div>
  <div class="tl-date" style="left:661px">17 November 2023</div>
  <div class="tl-date" style="left:818px">1 December 2023</div>
  <div class="tl-date" style="left:958px">15 December 2023</div>

  <svg style="position:absolute;left:0;top:0" width="1074" height="604" viewBox="0 0 1074 604" aria-hidden="true">
    <defs>
      <g id="cal"><rect x="-16" y="-13" width="32" height="28" rx="2" fill="#222"/><rect x="-13" y="-5" width="26" height="17" fill="#fff"/><rect x="-10" y="-17" width="4" height="8" fill="#222"/><rect x="6" y="-17" width="4" height="8" fill="#222"/><g fill="#222"><rect x="-10" y="-2" width="4" height="4"/><rect x="-3" y="-2" width="4" height="4"/><rect x="4" y="-2" width="4" height="4"/><rect x="-10" y="5" width="4" height="4"/><rect x="-3" y="5" width="4" height="4"/><rect x="4" y="5" width="4" height="4"/></g></g>
      <g id="pin"><circle cy="0" r="6" fill="var(--blue)"/><path d="M0 6v53" stroke="#222" stroke-width="1.3"/></g>
    </defs>
    <path d="M150 318H962" stroke="var(--blue)" stroke-width="3"/>
    <g transform="translate(194,225)"><use href="#cal"/></g><g transform="translate(194,259)"><use href="#pin"/></g>
    <g transform="translate(350,225)"><use href="#cal"/></g><g transform="translate(350,259)"><use href="#pin"/></g>
    <g transform="translate(491,225)"><use href="#cal"/></g><g transform="translate(491,259)"><use href="#pin"/></g>
    <g transform="translate(661,225)"><use href="#cal"/></g><g transform="translate(661,259)"><use href="#pin"/></g>
    <g transform="translate(818,225)"><use href="#cal"/></g><g transform="translate(818,259)"><use href="#pin"/></g>
    <g transform="translate(958,225)"><use href="#cal"/></g><g transform="translate(958,259)"><use href="#pin"/></g>
  </svg>

  <div class="tl-tag" style="top:307px">INDICATIVE DATE</div>
  <div class="tl-tag" style="top:373px;left:64px">STAGE</div>

  <div class="tl-node" style="left:194px"><i><svg width="40" height="40" viewBox="0 0 40 40" fill="none" stroke="#fff" stroke-width="2.5"><circle cx="17" cy="17" r="11"/><path d="M25 25l9 9"/><path d="M12 17h10M17 12v10"/></svg></i></div>
  <div class="tl-node" style="left:350px"><i><svg width="40" height="40" viewBox="0 0 40 40" fill="none" stroke="#fff" stroke-width="2.5"><circle cx="18" cy="18" r="12"/><path d="M13 18l4 4 7-8M27 27l8 8"/></svg></i></div>
  <div class="tl-node" style="left:491px"><i><svg width="40" height="40" viewBox="0 0 40 40" fill="none" stroke="#fff" stroke-width="2.5"><path d="M6 34h30M10 34V22M18 34V14M26 34V18M8 16l10-8 8 5 8-7"/></svg></i></div>
  <div class="tl-node" style="left:661px"><i><svg width="40" height="40" viewBox="0 0 40 40" fill="none" stroke="#fff" stroke-width="2.5"><circle cx="20" cy="20" r="12"/><path d="M20 13v9M20 26v1"/></svg></i></div>
  <div class="tl-node" style="left:818px"><i><svg width="40" height="40" viewBox="0 0 40 40" fill="none" stroke="#fff" stroke-width="2.5"><circle cx="16" cy="16" r="9"/><path d="M23 23l11 11M12 16h8"/></svg></i></div>
  <div class="tl-node" style="left:958px"><i><svg width="40" height="40" viewBox="0 0 40 40" fill="none" stroke="#fff" stroke-width="2.5"><rect x="6" y="8" width="22" height="24" rx="2"/><path d="M10 14h14M10 20h14M10 26h8"/><circle cx="30" cy="28" r="6"/></svg></i></div>

  <div class="tl-label" style="left:194px">PROJECT INCEPTION</div>
  <div class="tl-label" style="left:357px">SITUATION ANALYSIS</div>
  <div class="tl-label" style="left:494px">MARKET RESEARCH</div>
  <div class="tl-label" style="left:662px">ISSUES &amp; OPPORTUNITIES</div>
  <div class="tl-label" style="left:818px">ECONOMIC AND<br>ACCOUNTING ANALYSIS</div>
  <div class="tl-label" style="left:960px">FINAL REPORT</div>

  <div class="footer right">
    <div class="f-num" style="margin-right:50px">06</div>
    <div class="f-item" style="width:195px"><svg width="18" height="18" viewBox="0 0 18 18"><rect width="18" height="18" rx="3" fill="#fff"/><path d="M9 3a4 4 0 0 1 4 4c0 3-4 8-4 8S5 10 5 7a4 4 0 0 1 4-4z" fill="var(--blue)"/><circle cx="9" cy="7" r="1.5" fill="#fff"/></svg><span>Melbourne, Sydney, Brisbane,<br>Perth, Gold Coast, Hobart</span></div>
    <div class="f-item" style="width:140px"><svg width="16" height="16" viewBox="0 0 16 16"><rect width="16" height="16" rx="3" fill="#fff"/><path d="M5 3l2 3-1 1c.7 1.4 1.6 2.3 3 3l1-1 3 2-1 2c-4 0-8-4-8-8z" fill="var(--blue)"/></svg>+61 400 000 123</div>
    <div class="f-item"><svg width="14" height="11" viewBox="0 0 14 11"><rect x=".5" y=".5" width="13" height="10" rx="2" fill="#fff"/><path d="M2 2.5l5 4 5-4" stroke="var(--blue)" fill="none"/></svg>info@kelvara42.com.au</div>
  </div>
</section>

</body>
</html>
```